Create Website for new company called "Verdale Lodge 37"

Verdale Lodge 37 is a new business situated in Southwestern Colorado. We are creating a business that will rent out spaces where clients can grow their own marijuana. Picture a large green house with partitioned spaces that are secured by a lock. Best way to envision this would be to think of a storage business that rents out storage rooms. The difference is that we will be having the units inside a green house ( for growing purposes) Picture a small area that is secured by locks, Picture an area that has the ability to provide state of the art security, cameras etc. We want to focus our efforts on professionals, blue collar workers and end users of marijuana. Our emphasis is in the area of assisting those whom wish to grow their own plants. We want to provide them a safe facility in which to do that. . Keep in mind that we also build custom grow rooms at clients homes and provide a grow pod (lease these) where a small grow unit will be delivered and picked up from our clients whom want to lease a unit for a short amount of time. We have a business card ( just designed) and will send that information to those whom express an interests in this project. We want to be able to sign people up for our services by entering an agreement and signing the agreement while on the internet. We want to provide our services to those whom consume recreational and medical marijuana. This site will need to gather information I.e email addresses so that we can followup with offers. This is a tremendous opportunity for the right designer. We will be creating many more websites as other states come on line and make marijuana legal to consume. Use the business card model for a point of reference of how we envision the concept. That is a business card we just recently printed. The hands and the plant is our logo so far. Open to suggestions. There will be three levels of service. Bronze, Silver, Gold or Platinum. We will also have a retail biz down the road but not at the present time.

Target Market(s)

Ages 21-60

Industry/Entity Type

Medical

Logo Text

Verdale Lodge 37.

Number of Pages Required

5+ page

Requirements
Must have
• Clean appearance not to busy , easily navigable from link to link, page to page. Must have ability down the road to enter into a contractual agreement via the website. Must use our provided logo and example of that is on our business card that will be uploaded here shortly. We would like to have the colors that are on the business card however if you have suggestions or color schemes that you want us to consider that is okay.
Nice to have
• Nice to have a animation of seed to weed and how clients can save a tremendous amount of money growing their own cannabis. Nice to have testimonial page or feedback page. Have a membership component to website,
Should not have
• No flashing lights, etc. Not to busy in terms of animations.

```html
<!DOCTYPE html>
<html lang="en">
<head>
<meta charset="utf-8">
<title>Verdale Lodge 37</title>
<link href="https://fonts.googleapis.com/css2?family=Oswald:wght@400;500&family=Noticia+Text&family=Arimo:wght@400;700&display=swap" rel="stylesheet">
<style>
:root{
  --green:#047a38;
  --green-dark:#05672f;
  --green-light:#2a8f52;
  --page:#ebebeb;
  --ink:#3a3a3a;
  --text:#555;
  --bronze:#2f3436;
  --gold:#dc7b35;
  --white:#fff;
}
*{box-sizing:border-box;margin:0;padding:0}
html,body{width:937px;height:1200px;overflow:hidden;background:var(--white)}
body{position:relative;font-family:"Arimo",Arial,sans-serif;color:var(--text)}
.abs{position:absolute}

/* header */
.nav-ribbon{left:44px;top:78px;width:850px;height:57px}
.logo-panel{left:331px;top:0;width:277px;height:111px}
.brand{left:331px;top:52px;width:277px;text-align:center;font-family:"Oswald",sans-serif;font-weight:500;font-size:27px;color:var(--bronze);letter-spacing:.5px}
.brand-mark{left:454px;top:8px;width:32px;height:32px;border-radius:50%;background:var(--green)}
.nav a{position:absolute;top:90px;font-family:"Oswald",sans-serif;font-size:16px;color:var(--white);text-decoration:none}

/* hero */
.hero{left:68px;top:127px;width:802px;height:245px;background:linear-gradient(135deg,#4e8a2c 0%,#7fb447 35%,#5c9a33 60%,#a8b49a 85%,#6f9d3f 100%)}
.hero-caption{left:110px;top:239px;width:276px;height:86px;background:rgba(235,245,230,.55);border-radius:3px;text-align:center;font-family:"Oswald",sans-serif;font-size:25px;line-height:31px;color:var(--green);padding-top:10px}
.dot{top:348px;width:15px;height:15px;border-radius:50%;border:2px solid var(--white);background:rgba(255,255,255,.55)}
.dot.active{background:#555}

/* welcome */
.content-bg{left:68px;top:372px;width:802px;height:513px;background:var(--page)}
.welcome-title{left:79px;top:380px;font-family:"Noticia Text",serif;font-weight:400;font-size:20px;color:var(--ink)}
.welcome-title span{color:var(--green)}
.para{left:79px;width:526px;font-size:10.2px;line-height:13.9px;color:var(--text)}

/* signup */
.signup{left:616px;top:378px;width:246px;height:206px;background:var(--green-light);border:2px solid #11a64e;border-radius:4px;text-align:center}
.signup h2{font-family:"Noticia Text",serif;font-weight:400;font-size:19px;line-height:21px;color:var(--white);margin-top:4px}
.field{left:630px;width:220px;height:25px;background:var(--white);font-family:"Noticia Text",serif;font-size:12px;color:#888;padding:5px 6px}
.join{left:700px;top:509px;width:65px;height:25px;background:#f1f1f1;font-family:"Noticia Text",serif;font-size:15px;color:var(--green);text-align:center;line-height:25px}
.signup-links{left:616px;top:543px;width:246px;text-align:center;font-family:"Noticia Text",serif;font-size:11.5px;color:var(--white)}

/* services */
.rule{left:84px;top:602px;width:769px;height:2px;background:var(--white)}
.services-title{left:68px;top:610px;width:802px;text-align:center;font-family:"Noticia Text",serif;font-weight:400;font-size:18px;color:var(--green)}
.plan{top:638px;width:244px;height:221px;border:3px solid;border-radius:11px;text-align:center}
.plan h3{font-family:"Noticia Text",serif;font-weight:400;font-size:17px;line-height:22px;margin-top:5px}
.plan p{font-size:10px;line-height:13.6px;letter-spacing:.15px;text-align:justify;padding:0 11px;color:var(--text);margin-top:8px}
.plan p + p{margin-top:13px}
.buy{position:absolute;left:83px;top:182px;width:73px;height:25px;color:var(--white);font-family:"Noticia Text",serif;font-size:15px;line-height:25px;display:flex;align-items:center;justify-content:center;gap:5px}
.bronze{left:82px;border-color:var(--bronze)} .bronze h3{color:var(--bronze)} .bronze .buy{background:var(--bronze)}
.silver{left:351px;border-color:var(--green)} .silver h3{color:var(--green)} .silver .buy{background:var(--green)}
.gold{left:613px;border-color:var(--gold)} .gold h3{color:var(--gold)} .gold .buy{background:var(--gold)}

/* news band */
.band{left:68px;top:885px;width:802px;height:204px;background:var(--green)}
.band-title{top:893px;font-family:"Noticia Text",serif;font-weight:400;font-size:18px;line-height:24px;color:var(--white)}
.news-item{left:86px;width:393px;border-bottom:1px solid #9cc9ad;padding-bottom:4px}
.news-date{font-size:9.5px;color:#111}
.news-text{font-size:10.4px;line-height:13.9px;color:var(--white)}
.tweets-sub{left:501px;top:917px;font-size:12px;line-height:14px;color:#111}
.follow{left:691px;top:911px;width:168px;height:21px;background:#f0f0f0;border:1px solid #ccc;border-radius:3px;font-size:9.5px;color:#222;display:flex;align-items:center;gap:5px;padding-left:6px;white-space:nowrap}
.follow i{width:10px;height:10px;background:#3aa3e3;display:block;flex:none}
.avatar{left:501px;width:53px;height:52px;background:linear-gradient(#cdbfae,#8d7563)}
.tweet{left:561px;width:300px;font-size:9.4px;line-height:13.9px;color:var(--white)}
.tweet b{font-size:11px}
.tweet .exp{color:#111}
.tweet-rule{left:500px;top:1001px;width:362px;height:1px;background:#9cc9ad}

/* footer */
.footer{left:68px;top:1113px;width:802px;height:87px;background:var(--gold)}
.foot-nav{position:absolute;top:1132px;font-family:"Oswald",sans-serif;font-size:13px;color:var(--white)}
.foot-nav.current{color:#111}
.social{top:1122px;width:40px;height:40px;border-radius:50%;border:2px solid}
.copy{left:68px;top:1175px;width:802px;text-align:center;font-size:10px;color:var(--white)}
.copy u{font-weight:700}
</style>
</head>
<body>

<!-- header -->
<svg class="abs nav-ribbon" viewBox="0 0 850 57" aria-hidden="true">
  <polygon points="0,0 16,0 16,49 0,49 8,25" fill="#036630"/>
  <polygon points="850,0 834,0 834,49 850,49 842,25" fill="#036630"/>
  <rect x="16" y="0" width="818" height="49" fill="var(--green)"/>
  <polygon points="16,49 26,57 26,49" fill="#024f24"/>
  <polygon points="834,49 824,57 824,49" fill="#024f24"/>
</svg>
<svg class="abs logo-panel" viewBox="0 0 277 111" aria-hidden="true">
  <polygon points="0,0 277,0 277,80 138,111 0,80" fill="#e8e8e8"/>
</svg>
<div class="abs brand-mark"></div>
<div class="abs brand">VERDALE LODGE 37</div>
<nav class="nav">
  <a style="left:96px">HOME</a>
  <a style="left:165px">ABOUT</a>
  <a style="left:249px">SERVICES</a>
  <a style="left:582px">Blog</a>
  <a style="left:651px">TESTIMONIAL</a>
  <a style="left:765px">CONTACT US</a>
</nav>

<!-- hero -->
<div class="abs hero" role="img" aria-label="Close-up photograph of green cannabis leaves growing outdoors"></div>
<div class="abs hero-caption">Supporting the care &amp;<br>cultivation of cannabis</div>
<svg class="abs" style="left:83px;top:226px" width="18" height="42" aria-hidden="true"><polyline points="16,2 3,21 16,40" fill="none" stroke="#fff" stroke-width="2"/></svg>
<svg class="abs" style="left:837px;top:226px" width="18" height="42" aria-hidden="true"><polyline points="2,2 15,21 2,40" fill="none" stroke="#fff" stroke-width="2"/></svg>
<span class="abs dot active" style="left:424px"></span>
<span class="abs dot" style="left:449px"></span>
<span class="abs dot" style="left:473px"></span>
<span class="abs dot" style="left:497px"></span>

<!-- welcome -->
<div class="abs content-bg"></div>
<h1 class="abs welcome-title">Welcome to <span>VERDALE LODGE 37</span></h1>
<p class="abs para" style="top:406px">Lorem Ipsum is simply dummy text of the printing and typesetting industry. Lorem Ipsum has been the industry's standard dummy text ever since the 1500s, when an unknown printer took a galley of type and scrambled it to make a type specimen book. It has survived not only five centuries.</p>
<p class="abs para" style="top:462px">Lorem Ipsum is simply dummy text of the printing and typesetting industry. Lorem Ipsum has been the industry's standard Lorem Ipsum is simply dummy text of the printing and typesetting industry. Lorem Ipsum has been the industry's standard dummy text ever since the 1500s, when an unknown printer took a galley of type and scrambled it to make a type specimen book. It has survived not only five centuries.</p>
<p class="abs para" style="top:531px">Lorem Ipsum is simply dummy text of the printing and typesetting industry. Lorem Ipsum has been the industry's standard dummy text ever since the 1500s, when an unknown printer took a galley of type and scrambled it to make a type specimen book. It has survived not only five centuries.</p>

<!-- signup -->
<div class="abs signup"><h2>A Better Way<br>To Do Business</h2></div>
<div class="abs field" style="top:434px">Enter your name</div>
<div class="abs field" style="top:475px">Enter your Email</div>
<div class="abs join">JOIN</div>
<div class="abs signup-links">Login &nbsp;|&nbsp; Forget Password</div>

<!-- services -->
<div class="abs rule"></div>
<h2 class="abs services-title">SERVICES</h2>

<div class="abs plan bronze">
  <h3>Bronze</h3>
  <p>Lorem Ipsum is simply dummy text of the printing and typesetting industry. Lorem Ipsum has been the industry's standard dummy text ever since the 1500s, when an unknown printer took a galley of type and scrambled it to make a type specimen book.</p>
  <p>Lorem Ipsum is simply dummy text of the printing and typesetting industry. Lorem Ipsum has been the industry's standard</p>
  <div class="buy"><svg width="16" height="13" viewBox="0 0 16 13" aria-hidden="true"><path d="M0 1h3l2 7h8l2-5H4" fill="none" stroke="#fff" stroke-width="2"/><circle cx="6" cy="11" r="1.5" fill="#fff"/><circle cx="12" cy="11" r="1.5" fill="#fff"/></svg>BUY</div>
</div>
<div class="abs plan silver">
  <h3>Silver</h3>
  <p>Lorem Ipsum is simply dummy text of the printing and typesetting industry. Lorem Ipsum has been the industry's standard dummy text ever since the 1500s, when an unknown printer took a galley of type and scrambled it to make a type specimen book.</p>
  <p>Lorem Ipsum is simply dummy text of the printing and typesetting industry. Lorem Ipsum has been the industry's standard</p>
  <div class="buy"><svg width="16" height="13" viewBox="0 0 16 13" aria-hidden="true"><path d="M0 1h3l2 7h8l2-5H4" fill="none" stroke="#fff" stroke-width="2"/><circle cx="6" cy="11" r="1.5" fill="#fff"/><circle cx="12" cy="11" r="1.5" fill="#fff"/></svg>BUY</div>
</div>
<div class="abs plan gold">
  <h3>Gold</h3>
  <p>Lorem Ipsum is simply dummy text of the printing and typesetting industry. Lorem Ipsum has been the industry's standard dummy text ever since the 1500s, when an unknown printer took a galley of type and scrambled it to make a type specimen book.</p>
  <p>Lorem Ipsum is simply dummy text of the printing and typesetting industry. Lorem Ipsum has been the industry's standard</p>
  <div class="buy"><svg width="16" height="13" viewBox="0 0 16 13" aria-hidden="true"><path d="M0 1h3l2 7h8l2-5H4" fill="none" stroke="#fff" stroke-width="2"/><circle cx="6" cy="11" r="1.5" fill="#fff"/><circle cx="12" cy="11" r="1.5" fill="#fff"/></svg>BUY</div>
</div>

<!-- news & tweets -->
<div class="abs band"></div>
<h2 class="abs band-title" style="left:86px">Latest News</h2>
<div class="abs news-item" style="top:924px"><div class="news-date">Dec 17 2014</div><div class="news-text">Lorem Ipsum is simply dummy text of the printing and typesetting industry. Lorem Ipsum has been the industry's standard dummy text ever since the 1500s.</div></div>
<div class="abs news-item" style="top:973px"><div class="news-date">Dec 14 2014</div><div class="news-text">Lorem Ipsum is simply dummy text of the printing and typesetting industry. Lorem Ipsum has been the industry's standard dummy text ever since the 1500s.</div></div>
<div class="abs news-item" style="top:1023px"><div class="news-date">Dec 10 2014</div><div class="news-text">Lorem Ipsum is simply dummy text of the printing and typesetting industry.</div></div>

<h2 class="abs band-title" style="left:499px">Tweets</h2>
<div class="abs tweets-sub">Tweets</div>
<div class="abs follow"><i></i>Follow @VERDALE LODGE 37</div>

<div class="abs avatar" style="top:940px" role="img" aria-label="Profile photo of tweet author"></div>
<div class="abs tweet" style="top:940px"><b>Halvery</b> @ Halvery<br>Lorem Ipsum is simply dummy @ dummy text of the printing and typesetting industry. Lorem Ipsum has been the industry's standard<br><span class="exp">Expand</span></div>
<div class="abs tweet-rule"></div>
<div class="abs avatar" style="top:1010px" role="img" aria-label="Profile photo of tweet author"></div>
<div class="abs tweet" style="top:1010px"><b>Halvery</b> @ Halvery<br>Lorem Ipsum is simply dummy @ dummy text of the printing and typesetting industry. Lorem Ipsum has been.<br><span class="exp">Expand</span></div>

<!-- footer -->
<div class="abs footer"></div>
<span class="foot-nav current" style="left:96px">HOME</span>
<span class="foot-nav" style="left:161px">ABOUT</span>
<span class="foot-nav" style="left:231px">SERVICES</span>
<span class="foot-nav" style="left:315px">Blog</span>
<span class="foot-nav" style="left:376px">TESTIMONIAL</span>
<span class="foot-nav" style="left:475px">CONTACT US</span>
<span class="abs social" style="left:699px;background:var(--bronze);border-color:#111"></span>
<span class="abs social" style="left:756px;background:var(--green);border-color:#0b5a2c"></span>
<span class="abs social" style="left:813px;background:var(--green);border-color:#0b5a2c"></span>
<div class="abs copy">© <u>VERDALE LODGE 37</u> - 2014. All Rights Reserved.</div>

</body>
</html>
```